Flyer Design Project

We need a flyer for a company based in Melbourne, Australia.
We offer subscription based E-Commerce/CMS website starting from $20/month. We also do custom web design, custom software development and SEO as additional services.

KORVENTrade is our first product, where people can get their site up and running in just seconds.

We would like to designs that sticks to our company branding. Our main color is white/grey/green.
Our complementary color is dark grey and orange.

The final design should deliver the following elements:
- modern
- clean
- easy / playful / fun
- grow (in sales, business)
- friendly

Our goal is to deliver this message to small businesses:
Online shop / website that is
- affordable
- easy to use
- accessible from many devices

Overall look please visit www.korven-example.com.au

Target Market(s)

small business start ups

Industry/Entity Type

Software

Requirements
Must have
• Must look commercial / selling.
$20/month must be highlighted.
mascot, leaves
stick with the company branding.
Flowing design.

Please allocate a white box in (64mm x 24.3mm) for labelling.
Will be printed in A5, double sided.
Nice to have
• We are using DIN for KORVEN
and MyriadPro for "Market Your Goods Simply", be good if we can stick to the font.
May use the shop image in the attachment, not necessary.
Should not have
• Must not look old / corporate.

```html
<!DOCTYPE html>
<html lang="en">
<head>
<meta charset="utf-8">
<title>KORVEN Web Development Flyer</title>
<link rel="stylesheet" href="https://fonts.googleapis.com/css2?family=Source+Sans+3:wght@300;400;600;700&family=Barlow+Condensed:wght@600;700;800&display=swap">
<style>
  :root {
    --green: #8cc63f;
    --green-light: #a6d45a;
    --green-deep: #4f8a1e;
    --bubble: #3f7a17;
    --orange: #f26f21;
    --orange-light: #f7941d;
    --grey-dark: #555759;
    --grey: #6d6e70;
    --grey-light: #a7a9ac;
    --white: #ffffff;
    --ink: #111111;
    --sans: "Source Sans 3", "Myriad Pro", Arial, sans-serif;
    --condensed: "Barlow Condensed", "Arial Narrow", sans-serif;
  }
  * { box-sizing: border-box; margin: 0; padding: 0; }
  html, body { width: 1200px; height: 900px; overflow: hidden; background: var(--white); }
  .flyer { position: relative; width: 1200px; height: 900px; overflow: hidden; background: var(--white); font-family: var(--sans); color: var(--grey-dark); }
  .abs { position: absolute; }

  .band { left: 0; top: 0; width: 1200px; height: 900px; }
  .leaves { right: 0; top: 0; width: 360px; height: 200px; background: radial-gradient(ellipse at 70% 30%, rgba(140,198,63,.55), rgba(200,230,160,.25) 55%, rgba(255,255,255,0) 75%); }

  .brand { left: 0; width: 1200px; top: 22px; text-align: center; }
  .brand-name { font-family: var(--sans); font-weight: 300; font-size: 66px; letter-spacing: 4px; color: var(--grey-light); line-height: 1; }
  .brand-tag { font-size: 15px; color: var(--green); margin-top: 2px; padding-left: 150px; }

  .address { left: 0; width: 1200px; top: 122px; text-align: center; font-size: 21px; color: var(--grey-dark); }
  .phone { display: flex; align-items: center; gap: 6px; font-weight: 700; color: var(--grey-dark); }
  .phone .g { color: var(--green); }
  .phone-top { left: 500px; top: 158px; font-size: 29px; }
  .offer { left: 0; width: 1200px; top: 200px; text-align: center; font-size: 32px; line-height: 40px; color: var(--grey-dark); }
  .offer .price { color: var(--green); }

  .side-card { left: 14px; top: 240px; width: 276px; height: 470px; background: var(--white); border-radius: 12px; }
  .badge { left: 18px; top: 52px; width: 228px; height: 228px; border-radius: 50%; background: var(--orange); }
  .badge-inner { left: 32px; top: 66px; width: 200px; height: 200px; border-radius: 50%; background: var(--green); color: var(--white); text-align: center; }
  .badge-label { display: block; font-size: 31px; margin-top: 16px; line-height: 1; }
  .badge-price { display: block; font-family: var(--condensed); font-weight: 800; font-size: 112px; line-height: 92px; }
  .badge-unit { display: block; font-size: 24px; line-height: 1; }
  .shop-art { left: 36px; top: 282px; width: 228px; height: 174px; border-radius: 6px; background: linear-gradient(180deg, #9fd14f 0 22%, #e9f4dc 22% 100%); }
  .side-copy { left: 14px; top: 460px; width: 276px; text-align: center; font-size: 34px; line-height: 41px; color: var(--grey-dark); }
  .phone-side { left: 34px; top: 640px; font-size: 29px; }

  .package { left: 307px; top: 312px; }
  .package-title { font-size: 27px; font-weight: 700; color: var(--green-deep); line-height: 1; }
  .package-name { font-size: 17px; font-weight: 600; color: var(--white); }

  .plans { left: 306px; top: 379px; width: 534px; border-collapse: collapse; background: var(--white); color: var(--ink); font-size: 9.5px; }
  .plans th, .plans td { border: 1px solid #333; text-align: center; padding: 0 2px; }
  .plans th { font-size: 19px; font-weight: 400; height: 38px; }
  .plans td.term { font-weight: 700; vertical-align: top; padding-top: 3px; height: 30px; line-height: 1.1; }
  .plans td.term em { font-weight: 400; display: block; }
  .plans .tall td { vertical-align: top; padding-top: 3px; }
  .plans td { height: 15px; }
  .plans col.label { width: 138px; }

  .features-note { left: 307px; top: 612px; font-size: 30px; line-height: 38px; color: var(--white); }

  .services { left: 870px; top: 404px; color: var(--white); }
  .services-title { font-family: var(--condensed); font-weight: 700; font-size: 33px; color: var(--grey-dark); line-height: 1; }
  .services-list { list-style: none; font-family: var(--condensed); font-weight: 700; font-size: 21px; line-height: 25px; margin-top: 8px; }
  .services-list span { font-weight: 600; font-size: 18px; }
  .trial { left: 870px; top: 528px; width: 152px; height: 38px; border-radius: 4px; background: linear-gradient(180deg, var(--orange-light), var(--orange)); color: var(--white); font-family: var(--condensed); font-weight: 700; font-size: 19px; display: flex; align-items: center; justify-content: center; padding-left: 22px; overflow: hidden; }
  .trial-new { position: absolute; left: -12px; top: 5px; transform: rotate(-45deg); background: var(--grey-dark); font-size: 8px; padding: 1px 12px; }

  .mascot { border-radius: 14px; background: linear-gradient(180deg, #a9d94e, #7fb52e); }
  .mascot-top { left: 1002px; top: 204px; width: 120px; height: 204px; }
  .mascot-bottom { left: 1044px; top: 702px; width: 126px; height: 162px; }
  .bubble { left: 908px; top: 568px; width: 196px; height: 156px; }
  .bubble-text { left: 930px; top: 594px; width: 150px; text-align: center; font-size: 24px; font-weight: 700; line-height: 32px; color: var(--white); }

  .van { left: 18px; top: 780px; width: 210px; height: 96px; border-radius: 30px 40px 12px 12px; background: linear-gradient(180deg, #f2f2f2, #d6d8da); }
  .slogan { left: 252px; top: 770px; font-size: 64px; line-height: 1; color: var(--grey); }
  .slogan .g { color: var(--green); }
  .url { left: 0; width: 1200px; top: 848px; text-align: center; font-size: 34px; color: var(--grey); }
</style>
</head>
<body>
<div class="flyer">

  <svg class="abs band" viewBox="0 0 1200 900" aria-hidden="true">
    <path d="M0,246 C260,232 420,262 640,270 C860,278 1020,250 1200,262 L1200,790 C1020,760 860,730 640,732 C420,734 220,712 0,704 Z" fill="var(--green)"/>
    <path d="M300,300 C520,282 760,300 1200,282 L1200,300 C760,320 520,300 300,318 Z" fill="var(--green-light)" opacity=".6"/>
    <path d="M0,714 C260,724 460,760 700,752 C900,745 1060,760 1200,800 L1200,812 C1060,774 900,760 700,766 C460,774 260,738 0,728 Z" fill="var(--white)" opacity=".7"/>
  </svg>

  <div class="abs leaves" role="img" aria-label="Fresh green leaves on a branch"></div>

  <header class="abs brand">
    <div class="brand-name">KORVEN</div>
    <div class="brand-tag">web development</div>
  </header>

  <p class="abs address">Address: 4/52 Kestrel Lane Riverbend VIC - 3999 Melbourne</p>

  <div class="abs phone phone-top">
    <svg width="36" height="28" viewBox="0 0 36 28" aria-hidden="true"><path d="M4,12 C4,6 32,6 32,12 L28,15 L23,12 L23,9 C19,8 17,8 13,9 L13,12 L8,15 Z" fill="var(--green)"/><rect x="9" y="15" width="18" height="11" rx="3" fill="var(--green)"/><path d="M2,7 C6,1 12,0 14,1" stroke="var(--grey-dark)" stroke-width="2" fill="none"/></svg>
    <span>1300 <span class="g">55</span> 01 <span class="g">73</span></span>
  </div>

  <p class="abs offer">We offer subscription based E-Commerce/CMS<br>website starting from <span class="price">$20/month</span></p>

  <aside class="abs side-card"></aside>
  <div class="abs badge"></div>
  <div class="abs badge-inner">
    <span class="badge-label">Website @</span>
    <span class="badge-price">$20</span>
    <span class="badge-unit">month</span>
  </div>
  <div class="abs shop-art" role="img" aria-label="Small shop front with a green striped awning and a mascot beside the door"></div>
  <p class="abs side-copy">All you need<br>to open a<br>Successful<br>Online Store</p>
  <div class="abs phone phone-side">
    <svg width="36" height="28" viewBox="0 0 36 28" aria-hidden="true"><path d="M4,12 C4,6 32,6 32,12 L28,15 L23,12 L23,9 C19,8 17,8 13,9 L13,12 L8,15 Z" fill="var(--green)"/><rect x="9" y="15" width="18" height="11" rx="3" fill="var(--green)"/><path d="M2,7 C6,1 12,0 14,1" stroke="var(--grey-dark)" stroke-width="2" fill="none"/></svg>
    <span>1300 <span class="g">55</span> 01 <span class="g">73</span></span>
  </div>

  <div class="abs package">
    <h2 class="package-title">Product Package</h2>
    <p class="package-name">Product Name: KORVENTrade</p>
  </div>

  <table class="abs plans">
    <colgroup><col class="label"><col><col><col><col></colgroup>
    <thead>
      <tr><th></th><th>Sprout</th><th>Root</th><th>Plan</th><th>Tree</th></tr>
    </thead>
    <tbody>
      <tr class="tall"><td class="term">Yearly<em>12 months</em></td><td>$20/Month</td><td>$40/Month</td><td>$80/Month</td><td>$100/Month</td></tr>
      <tr class="tall"><td class="term">Quarterly<em>3 months</em></td><td>$2/Month</td><td>$50/Month</td><td>$100/Month</td><td>$125/Month</td></tr>
      <tr><td>Max. Products</td><td>100</td><td>500</td><td>2000</td><td>5000</td></tr>
      <tr><td>Max. Pages</td><td>10</td><td>50</td><td>200</td><td>500</td></tr>
      <tr><td>Max. Storage</td><td>250MB</td><td>500MB</td><td>1GB</td><td>2.5GB</td></tr>
      <tr><td>0% Transaction Fee</td><td>x</td><td>x</td><td>x</td><td>x</td></tr>
      <tr><td>Fee Set up</td><td>x</td><td>x</td><td>x</td><td>x</td></tr>
      <tr><td>Free Upgrade</td><td>x</td><td>x</td><td>x</td><td>x</td></tr>
      <tr><td>Unlimited Users</td><td>x</td><td>x</td><td>x</td><td>x</td></tr>
      <tr><td>Unlimited Bandwidth</td><td>x</td><td>x</td><td>x</td><td>x</td></tr>
    </tbody>
  </table>

  <p class="abs features-note">Every plan comes with full feature<br>of KORVENTrade</p>

  <section class="abs services">
    <h2 class="services-title">Additional Services:</h2>
    <ul class="services-list">
      <li>Custom Web Design</li>
      <li>Custom Web Development</li>
      <li>SEO <span>(Search Engine Optimisation)</span></li>
    </ul>
  </section>
  <div class="abs trial"><span class="trial-new">NEW</span>FREE TRIAL</div>

  <div class="abs mascot mascot-top" role="img" aria-label="Green box-shaped mascot wearing a tie"></div>

  <svg class="abs bubble" viewBox="0 0 196 156" aria-hidden="true">
    <path d="M98,4 C150,4 192,30 192,66 C192,96 168,118 136,126 L176,152 L112,128 C104,129 100,130 98,130 C46,130 4,102 4,66 C4,30 46,4 98,4 Z" fill="var(--bubble)"/>
  </svg>
  <p class="abs bubble-text">Start<br>Selling<br>Today!</p>

  <div class="abs mascot mascot-bottom" role="img" aria-label="Green box-shaped mascot with an orange antenna"></div>

  <div class="abs van" role="img" aria-label="White company van with green leaf livery"></div>

  <h1 class="abs slogan">Market <span class="g">Your Goods</span> <span class="g">Simply</span></h1>
  <p class="abs url">www.korven-example.com.au</p>
</div>
</body>
</html>
```